Birchline Septic Solutions

Would like to see some single sided ones but would also like to see some double sided with one sided only being the logo. Owners name is Colin Vandro. Phone number is 555-214-0387
Services are pumping, inspections, installs, and repairs

Contact Information for Business Card

555-241-0387 Colin Vandro Fernridge, OH

```html
<!DOCTYPE html>
<html lang="en">
<head>
<meta charset="utf-8">
<title>Birchline Septic Solutions – Business Card</title>
<link rel="stylesheet" href="https://fonts.googleapis.com/css2?family=Montserrat:wght@500;600;800&display=swap">
<style>
  :root {
    --backdrop: #2a2a2e;
    --card: #1c1c1e;
    --teal: #2bb3ad;
    --white: #f4f4f4;
    --emboss: #2e2e31;
  }
  * { margin: 0; padding: 0; box-sizing: border-box; }
  html, body {
    width: 1200px;
    height: 948px;
    overflow: hidden;
    background: var(--backdrop);
    font-family: "Montserrat", sans-serif;
  }
  .sheet {
    position: relative;
    width: 1200px;
    height: 948px;
    display: flex;
    flex-direction: column;
    align-items: center;
    justify-content: center;
    gap: 24px;
  }
  .card {
    position: relative;
    width: 760px;
    height: 434px;
    background: var(--card);
    border-radius: 26px;
    border-bottom: 5px solid var(--teal);
    overflow: hidden;
  }
  .brand {
    display: flex;
    align-items: center;
    gap: 16px;
  }
  .brand__mark {
    flex: none;
    width: 18px;
    height: 18px;
    background: currentColor;
  }
  .brand__name {
    font-weight: 800;
    text-transform: uppercase;
    letter-spacing: 0.04em;
    line-height: 1.12;
    white-space: nowrap;
  }

  /* Logo-only side */
  .card--back {
    display: flex;
    align-items: center;
    justify-content: center;
  }
  .card--back .brand { color: var(--emboss); }
  .card--back .brand__name { font-size: 46px; }

  /* Contact side */
  .card--front .brand {
    position: absolute;
    top: 56px;
    right: 56px;
    color: var(--white);
  }
  .card--front .brand__name { font-size: 26px; text-align: right; }
  .rule {
    display: block;
    height: 2px;
    background: var(--teal);
  }
  .rule--top {
    position: absolute;
    top: 150px;
    left: 56px;
    right: 56px;
  }
  .contact {
    position: absolute;
    left: 56px;
    right: 56px;
    bottom: 52px;
  }
  .contact__name {
    color: var(--teal);
    font-weight: 800;
    font-size: 44px;
    letter-spacing: 0.02em;
    text-transform: uppercase;
    line-height: 1.1;
  }
  .contact__place {
    color: var(--white);
    font-weight: 500;
    font-size: 26px;
    margin-top: 6px;
  }
  .rule--mid {
    width: 100%;
    margin: 20px 0 18px;
  }
  .contact__phone {
    display: flex;
    align-items: center;
    gap: 16px;
    color: var(--white);
    font-weight: 600;
    font-size: 36px;
  }
  .contact__phone svg { width: 34px; height: 34px; fill: var(--teal); }
</style>
</head>
<body>
  <main class="sheet">
    <section class="card card--back" aria-label="Card back">
      <div class="brand">
        <span class="brand__mark"></span>
        <span class="brand__name">Birchline<br>Septic Solutions</span>
      </div>
    </section>

    <section class="card card--front" aria-label="Card front">
      <div class="brand">
        <span class="brand__name">Birchline<br>Septic Solutions</span>
      </div>
      <span class="rule rule--top"></span>
      <div class="contact">
        <p class="contact__name">Colin Vandro</p>
        <p class="contact__place">Fernridge, OH</p>
        <span class="rule rule--mid"></span>
        <p class="contact__phone">
          <svg viewBox="0 0 24 24" aria-hidden="true"><path d="M6.6 10.8a15.1 15.1 0 0 0 6.6 6.6l2.2-2.2a1 1 0 0 1 1-.25 11.4 11.4 0 0 0 3.6.57 1 1 0 0 1 1 1V20a1 1 0 0 1-1 1A17 17 0 0 1 3 4a1 1 0 0 1 1-1h3.5a1 1 0 0 1 1 1c0 1.25.2 2.45.57 3.57a1 1 0 0 1-.25 1z"/></svg>
          555-241-0387
        </p>
      </div>
    </section>
  </main>
</body>
</html>
```